I need a business card design for a new business based in South West Australia.
I specialize in residential window cleaning & general handyman maintenance.

Dale Marsh - 412 SILVER HAWK DETAILING
- Window Cleaning
- House Maintenance

```html
<!DOCTYPE html>
<html lang="en">
<head>
<meta charset="utf-8">
<title>Silver Hawk Detailing – Business Card</title>
<link rel="stylesheet" href="https://fonts.googleapis.com/css2?family=Open+Sans:wght@300;400;600&display=swap">
<style>
  :root {
    --backdrop: #c9b697;
    --card-black: #151515;
    --band-blue: #4b9bd8;
    --glass-light: #c9d6e0;
    --glass-mid: #8fa4b4;
    --title-yellow: #f3e21b;
    --text-white: #f2f2f2;
    --text-soft: #dcdcdc;
  }
  * { margin: 0; padding: 0; box-sizing: border-box; }
  html, body {
    width: 1200px;
    height: 892px;
    overflow: hidden;
    background: var(--backdrop);
    font-family: "Open Sans", sans-serif;
  }
  .stage {
    position: relative;
    width: 1200px;
    height: 892px;
  }
  .business-card {
    position: absolute;
    left: 160px;
    top: 196px;
    width: 880px;
    height: 500px;
    border-radius: 24px;
    overflow: hidden;
    background: var(--card-black);
    box-shadow: 0 18px 40px rgba(0, 0, 0, 0.35);
  }
  .card-art {
    position: absolute;
    inset: 0;
    width: 880px;
    height: 500px;
  }
  .brand-name {
    position: absolute;
    left: 410px;
    top: 168px;
    color: var(--title-yellow);
    font-size: 38px;
    font-weight: 400;
    letter-spacing: 0.5px;
    white-space: nowrap;
  }
  .service-list {
    position: absolute;
    right: 46px;
    top: 232px;
    list-style: none;
    text-align: right;
  }
  .service-item {
    display: flex;
    align-items: center;
    justify-content: flex-end;
    gap: 16px;
    color: var(--text-soft);
    font-size: 25px;
    font-weight: 300;
    line-height: 44px;
  }
  .service-marker {
    width: 14px;
    height: 14px;
    border-radius: 50%;
    background: var(--text-white);
  }
  .contact {
    position: absolute;
    left: 262px;
    top: 352px;
    color: var(--text-white);
  }
  .contact-name {
    font-size: 38px;
    font-weight: 400;
    line-height: 48px;
  }
  .contact-phone {
    display: flex;
    align-items: center;
    gap: 14px;
    margin-top: 8px;
    font-size: 25px;
    font-weight: 300;
    color: var(--text-soft);
  }
  .phone-icon {
    width: 22px;
    height: 22px;
  }
</style>
</head>
<body>
<main class="stage">
  <section class="business-card">
    <svg class="card-art" viewBox="0 0 880 500" xmlns="http://www.w3.org/2000/svg">
      <defs>
        <linearGradient id="glassTone" x1="0" y1="0" x2="1" y2="1">
          <stop offset="0" stop-color="var(--glass-light)"/>
          <stop offset="0.55" stop-color="var(--glass-mid)"/>
          <stop offset="1" stop-color="var(--glass-light)"/>
        </linearGradient>
      </defs>
      <rect class="window-photo" x="0" y="0" width="880" height="500" fill="url(#glassTone)"
            role="img" aria-label="Photo of a squeegee wiping soapy water off a window pane"/>
      <path class="blue-band" d="M60 500 C150 290 340 40 610 0 L880 0 L880 500 Z" fill="var(--band-blue)"/>
      <path class="black-panel" d="M150 500 C240 300 430 80 720 0 L880 0 L880 500 Z" fill="var(--card-black)"/>
    </svg>

    <h1 class="brand-name">SILVER HAWK DETAILING</h1>

    <ul class="service-list">
      <li class="service-item">House Maintenance <span class="service-marker"></span></li>
      <li class="service-item">Window Cleaning <span class="service-marker"></span></li>
    </ul>

    <div class="contact">
      <p class="contact-name">Dale Marsh</p>
      <p class="contact-phone">
        <svg class="phone-icon" viewBox="0 0 24 24" xmlns="http://www.w3.org/2000/svg" aria-hidden="true">
          <rect x="0" y="0" width="24" height="24" rx="3" fill="var(--text-white)"/>
          <path d="M8 5 C6 6 5.5 8 6.5 10.5 C8 14 10 16 13.5 17.5 C16 18.5 18 18 19 16 L16.5 13.8 L14.6 15 C12.3 13.9 10.1 11.7 9 9.4 L10.2 7.5 Z" fill="var(--card-black)"/>
        </svg>
        0412 586 204
      </p>
    </div>
  </section>
</main>
</body>
</html>
```